Baby Boutique Needs a Business Card Design

We need a modern double sided business card design using the attached logo for Little Wren Nook.

Little Wren Nook is a baby boutique which sells only handmade clothing and accessories for both boys and girls. Our store will live exclusively online.

We would like to only use the colors that have been used in the logo.

Target Market(s)

Potential wholesale clients, Small business owners

Industry/Entity Type

Retail

Contact Information for Business Card

Name Gideon R. Falkner (Owner)
Email sales@littlewrennook.example
Main Phone 555-203-7719
Cell phone 555-203-7746
Website www.LittleWrenNook.example

Font styles to use
Sans Serif

Colors

Designer to choose colors to be used in the design.

Requirements
Must have
• -Would like to have icons that indentify the contact information.
• -Include our website
• -Include our tagline in a small area near the bottom. "Handmade Baby Creations"
• -Would like to include Facebook and Instagram Icons
• -
Nice to have
• Would like to have a simple back side with the logo.
• Something along the lines of the meadowfield lending card attached.

```html
<!DOCTYPE html>
<html lang="en">
<head>
<meta charset="utf-8">
<title>Little Wren Nook – Business Card</title>
<link rel="stylesheet" href="https://fonts.googleapis.com/css2?family=Work+Sans:wght@400;500;600&display=swap">
<style>
  :root {
    --stage: #3a3330;
    --card-black: #1c1c1c;
    --teal: #6fd3c0;
    --coral: #ec6461;
    --paper: #ffffff;
    --ink-light: #f2f2f2;
  }
  * { box-sizing: border-box; margin: 0; padding: 0; }
  html, body {
    width: 1200px; height: 715px; overflow: hidden;
    background: var(--stage);
    font-family: "Work Sans", Arial, sans-serif;
  }
  .canvas {
    position: relative; width: 1200px; height: 715px;
    display: flex; align-items: center; justify-content: center; gap: 50px;
  }
  .card {
    position: relative; width: 540px; height: 309px;
    background: var(--card-black);
    border-radius: 3px; overflow: hidden;
    box-shadow: 0 12px 30px rgba(0,0,0,.45);
  }
  /* Back side */
  .card--back { display: flex; flex-direction: column; align-items: center; justify-content: center; gap: 14px; }
  .brand-name {
    color: var(--teal); font-weight: 600; letter-spacing: .5px;
    display: flex; align-items: center; gap: 10px; white-space: nowrap;
  }
  .card--back .brand-name { font-size: 34px; }
  .brand-mark { width: 12px; height: 12px; border-radius: 50%; background: var(--coral); }
  .brand-art {
    width: 150px; height: 22px; border-radius: 11px;
    background: linear-gradient(90deg, rgba(236,100,97,.12), rgba(236,100,97,.5));
  }
  /* Front side */
  .card--front .brand-name { position: absolute; left: 30px; top: 30px; font-size: 24px; }
  .card--front .brand-art.small { position: absolute; left: 52px; top: 70px; width: 110px; height: 16px; }
  .owner { position: absolute; right: 34px; top: 112px; text-align: right; }
  .owner__name { color: var(--coral); font-size: 21px; font-weight: 500; letter-spacing: .5px; white-space: nowrap; }
  .owner__role { color: var(--teal); font-size: 13px; margin-top: 2px; }
  .owner-bar {
    position: absolute; right: 14px; top: 140px; width: 10px; height: 34px;
    background: var(--coral); border-left: 3px solid var(--teal);
  }
  .social { position: absolute; right: 36px; top: 186px; display: flex; gap: 10px; }
  .social__icon { width: 18px; height: 18px; fill: none; stroke: var(--coral); stroke-width: 2; }
  .contacts {
    position: absolute; left: 30px; top: 108px; list-style: none;
    color: var(--ink-light); font-size: 13px; line-height: 20px;
  }
  .contacts li { display: flex; align-items: center; gap: 9px; white-space: nowrap; }
  .contacts svg { width: 10px; height: 10px; fill: var(--coral); flex: none; }
  .wave { position: absolute; left: 0; top: 0; width: 540px; height: 309px; }
  .stork-art {
    position: absolute; left: 225px; top: 140px; width: 235px; height: 62px;
    background: linear-gradient(100deg, rgba(236,100,97,.05), rgba(236,100,97,.32));
    border-radius: 30px 8px 30px 8px;
  }
  .tagline {
    position: absolute; left: 150px; bottom: 16px;
    color: var(--coral); font-size: 15px; letter-spacing: .4px; white-space: nowrap;
  }
</style>
</head>
<body>
<main class="canvas">
  <section class="card card--back" aria-label="Card back">
    <div class="brand-name"><span class="brand-mark"></span>Little Wren Nook</div>
    <div class="brand-art" role="img" aria-label="Line-drawn stork carrying a bundle"></div>
  </section>

  <section class="card card--front" aria-label="Card front">
    <svg class="wave" viewBox="0 0 540 309" aria-hidden="true">
      <path d="M0 212 C150 218 300 245 440 309 L0 309 Z" fill="var(--paper)"/>
      <path d="M0 212 C150 218 300 245 440 309" fill="none" stroke="var(--coral)" stroke-width="3"/>
    </svg>
    <div class="brand-name"><span class="brand-mark"></span>Little Wren Nook</div>
    <div class="brand-art small" role="img" aria-label="Line-drawn stork carrying a bundle"></div>

    <ul class="contacts">
      <li><svg viewBox="0 0 10 10"><path d="M2 0h2l1 3-1.5 1a6 6 0 0 0 2.5 2.5L7 5l3 1v2c0 1-1 2-2 2A8 8 0 0 1 0 2c0-1 1-2 2-2z"/></svg>555-203-7719</li>
      <li><svg viewBox="0 0 10 10"><path d="M2.5 0h5a1 1 0 0 1 1 1v8a1 1 0 0 1-1 1h-5a1 1 0 0 1-1-1V1a1 1 0 0 1 1-1zm0 1.5v6h5v-6z"/></svg>555-203-7746</li>
      <li><svg viewBox="0 0 10 10"><path d="M0 2h10v6H0zM1 3v.3l4 2.5 4-2.5V3L5 5.4z"/></svg>sales@littlewrennook.example</li>
      <li><svg viewBox="0 0 10 10"><path d="M5 0a5 5 0 1 0 0 10A5 5 0 0 0 5 0zm0 1.2c.8.9 1.2 2.2 1.3 3.3H3.7C3.8 3.4 4.2 2.1 5 1.2zM3.7 5.5h2.6c-.1 1.1-.5 2.4-1.3 3.3-.8-.9-1.2-2.2-1.3-3.3z"/></svg>www.LittleWrenNook.example</li>
    </ul>

    <div class="owner">
      <div class="owner__name">Gideon R. Falkner</div>
      <div class="owner__role">Owner</div>
    </div>
    <div class="owner-bar"></div>
    <div class="social" aria-label="Social links">
      <svg class="social__icon" viewBox="0 0 18 18" aria-hidden="true"><circle cx="9" cy="9" r="7.5"/></svg>
      <svg class="social__icon" viewBox="0 0 18 18" aria-hidden="true"><circle cx="9" cy="9" r="7.5"/></svg>
    </div>

    <div class="stork-art" role="img" aria-label="Large line-drawn stork carrying a bundle"></div>
    <p class="tagline">Handmade Baby Creations</p>
  </section>
</main>
</body>
</html>
```